WordPress Design for both website and landing page for an expert

I need a clean and stylish design for my new website. I work as an expert (see attached file WHY HOW WHAT), my product is expert opinion (reports) for company evaluations You can use all of the attached pictures colored or black / white. The person is me, you can add other pictures, if you want. The design should be clean and stylish, so you could use white, black, gray, silver and / or one additional color. I have added an idea about my website, see attached file CONCEPT WEBSITE If you have any more information, please do not hesitate to contact us 'Hesitate to ask me ...

```html
<!DOCTYPE html>
<html lang="en">
<head>
<meta charset="utf-8">
<title>Lukas Brenner – Sachverständiger für Firmenbewertungen</title>
<link href="https://fonts.googleapis.com/css2?family=Montserrat:wght@400;500;600;700&family=Noto+Serif:wght@400&display=swap" rel="stylesheet">
<style>
  :root {
    --white: #ffffff;
    --ink: #23262b;
    --muted: #8d9196;
    --soft-bg: #eef1f4;
    --line: #c9cdd2;
    --footer: #3b3f46;
    --footer-text: #a9adb3;
    --hero-dark: #3c3c3c;
    --hero-mid: #6e6e6e;
    --hero-light: #b9b9b9;
    --nav-active: #9aa0a6;
  }
  * { box-sizing: border-box; margin: 0; padding: 0; }
  html, body { width: 1200px; height: 2314px; overflow: hidden; }
  body {
    position: relative;
    background: var(--white);
    font-family: "Montserrat", Arial, sans-serif;
    color: var(--ink);
  }

  /* Hero */
  .hero { position: absolute; left: 0; top: 0; width: 1200px; height: 771px; overflow: hidden; }
  .hero-photo {
    position: absolute; inset: 0;
    background:
      radial-gradient(ellipse 380px 520px at 820px 330px, var(--hero-mid) 0%, rgba(110,110,110,0) 100%),
      radial-gradient(ellipse 300px 300px at 1050px 600px, var(--hero-light) 0%, rgba(185,185,185,0) 100%),
      linear-gradient(100deg, #4a4a4a 0%, var(--hero-dark) 40%, #5a5a5a 70%, #8a8a8a 100%);
  }
  .brand {
    position: absolute; left: 68px; top: 62px;
    font-size: 19px; font-weight: 400; letter-spacing: 3px;
    color: var(--white); text-transform: uppercase;
  }
  .main-nav { position: absolute; top: 60px; left: 0; width: 1200px; height: 16px; }
  .main-nav a {
    position: absolute; top: 0;
    font-size: 12px; font-weight: 600; letter-spacing: 1.6px;
    color: var(--white); text-decoration: none; text-transform: uppercase;
  }
  .main-nav a.is-active { color: var(--nav-active); }
  .hero-title {
    position: absolute; left: 136px; top: 302px;
    font-size: 41px; font-weight: 500; letter-spacing: 3px; line-height: 51px;
    color: var(--white); text-transform: uppercase;
  }
  .hero-lead {
    position: absolute; left: 136px; top: 422px;
    font-size: 16.5px; line-height: 25px; color: var(--white);
  }
  .btn {
    position: absolute; display: flex; align-items: center; justify-content: center;
    border-radius: 20px; font-size: 12px; font-weight: 700; letter-spacing: 1.6px;
    text-transform: uppercase; text-decoration: none;
  }
  .btn-light { left: 137px; top: 534px; width: 215px; height: 40px; border: 2px solid var(--white); color: var(--white); }
  .scroll-hint { position: absolute; left: 591px; top: 690px; }

  /* Section headings */
  .section-title {
    position: absolute; left: 0; width: 1200px; text-align: center;
    font-size: 25px; font-weight: 500; line-height: 39px; color: var(--ink);
  }
  .serif { font-family: "Noto Serif", Georgia, serif; color: var(--muted); }

  /* Motives */
  .motives { position: absolute; left: 0; top: 771px; width: 1200px; height: 423px; background: var(--soft-bg); }
  .motive { position: absolute; top: 187px; width: 280px; font-size: 13.5px; line-height: 26px; }
  .motive-icon { position: absolute; left: 18px; top: -18px; }
  .pager { position: absolute; top: 298px; left: 583px; display: flex; gap: 8px; }
  .pager span { width: 12px; height: 12px; border: 1.5px solid var(--muted); border-radius: 50%; position: relative; }
  .pager span.is-current::after { content: ""; position: absolute; left: 2.5px; top: 2.5px; width: 4px; height: 4px; border-radius: 50%; background: var(--muted); }
  .divider { position: absolute; left: 137px; top: 355px; width: 926px; height: 1px; background: var(--line); }
  .note { position: absolute; top: 376px; left: 0; width: 1200px; text-align: center; font-size: 11px; line-height: 16px; color: var(--muted); }
  .note strong { color: #6b6f74; }

  /* Reasons */
  .reasons { position: absolute; left: 0; top: 1194px; width: 1200px; height: 746px; background: var(--white); }
  .timeline-line { position: absolute; left: 599px; top: 160px; width: 2px; height: 517px; background: #d5d8dc; }
  .timeline-node {
    position: absolute; left: 566px; width: 68px; height: 68px; border-radius: 50%;
    background: var(--white); border: 1.5px solid #cfd3d7;
    display: flex; align-items: center; justify-content: center;
  }
  .timeline-node.is-filled { background: var(--footer); border-color: var(--footer); }
  .reason { position: absolute; width: 240px; }
  .reason h3 { font-size: 15px; font-weight: 700; letter-spacing: 3px; text-transform: uppercase; line-height: 20px; }
  .reason p { font-size: 13.5px; line-height: 26px; margin-top: 4px; }
  .reason.is-left { text-align: right; }

  /* Promise */
  .promise { position: absolute; left: 0; top: 1940px; width: 1200px; height: 306px; background: var(--soft-bg); }
  .promise-text { position: absolute; top: 112px; left: 0; width: 1200px; text-align: center; font-size: 13.5px; line-height: 26px; }
  .btn-outline { left: 494px; top: 196px; width: 212px; height: 40px; border: 1.5px solid #9ea3a8; color: var(--ink); }

  /* Footer */
  .site-footer { position: absolute; left: 0; top: 2246px; width: 1200px; height: 68px; background: var(--footer); }
  .site-footer small { position: absolute; left: 137px; top: 27px; font-size: 11px; color: var(--footer-text); }
  .legal-links { position: absolute; right: 136px; top: 27px; font-size: 11px; color: var(--footer-text); }
  .legal-links span { margin: 0 8px; }
  .to-top { position: absolute; left: 1110px; top: 13px; width: 42px; height: 42px; border-radius: 50%; background: #6f747b; display: flex; align-items: center; justify-content: center; }
</style>
</head>
<body>

<header class="hero">
  <div class="hero-photo" role="img" aria-label="Black and white portrait photo of the valuation expert"></div>
  <div class="brand">Lukas Brenner</div>
  <nav class="main-nav">
    <a class="is-active" href="#" style="left:592px">Home</a>
    <a href="#" style="left:672px">About</a>
    <a href="#" style="left:762px">What I do</a>
    <a href="#" style="left:885px">Why / How I do</a>
    <a href="#" style="left:1055px">Contact</a>
  </nav>
  <h1 class="hero-title">Sachverständiger<br>für Firmenbewertungen</h1>
  <p class="hero-lead">Sie benötigen ein Gutachten zur Ermittlung<br>Ihres Unternehmenswertes</p>
  <a class="btn btn-light" href="#">Contact now!</a>
  <svg class="scroll-hint" width="18" height="12" viewBox="0 0 18 12"><path d="M1 2 L9 10 L17 2" fill="none" stroke="#ffffff" stroke-width="1.6"/></svg>
</header>

<section class="motives">
  <h2 class="section-title" style="top:60px">What are the buying motives<br>of the customers?</h2>
  <div class="motive serif" style="left:282px">
    <svg class="motive-icon" width="34" height="20" viewBox="0 0 34 20"><path d="M2 19 A15 15 0 0 1 32 19" fill="none" stroke="#d4d8dc" stroke-width="1.5"/></svg>
    You want to transfer your business to your heirs and need a valuation for the tax office?
  </div>
  <div class="motive serif" style="left:634px">
    <svg class="motive-icon" width="34" height="20" viewBox="0 0 34 20"><path d="M2 19 A15 15 0 0 1 32 19" fill="none" stroke="#d4d8dc" stroke-width="1.5"/></svg>
    You have to pay someone in the context of a separation / divorce and need a tax base?
  </div>
  <div class="pager"><span class="is-current"></span><span></span></div>
  <div class="divider"></div>
  <p class="note"><strong>Note:</strong> The cost of a report are always disproportionately cheaper than the cost of legal disputes.<br>And that detached from the psychological burden of such an argument ...</p>
</section>

<section class="reasons">
  <h2 class="section-title" style="top:60px">Reasons, what you need<br>a report for</h2>
  <div class="timeline-line"></div>

  <div class="timeline-node" style="top:203px">
    <svg width="22" height="22" viewBox="0 0 22 22" fill="none" stroke="#4a4e54" stroke-width="1.4"><rect x="2" y="4" width="18" height="16"/><path d="M2 8h18M7 2v4M15 2v4M6 12h2M10 12h2M14 12h2M6 16h2M10 16h2M14 16h2"/></svg>
  </div>
  <div class="reason" style="left:668px;top:209px">
    <h3>Fast process</h3>
    <p class="serif">You will receive your report promptly (within a maximum of 21 days after receipt of all required documents)</p>
  </div>

  <div class="timeline-node is-filled" style="top:358px">
    <svg width="24" height="26" viewBox="0 0 24 26" fill="none" stroke="#ffffff" stroke-width="1.4"><circle cx="12" cy="10" r="7"/><circle cx="12" cy="10" r="3.5"/><path d="M7 15 L4 24 L8 22 L10 25 L12 17 M17 15 L20 24 L16 22 L14 25 L12 17"/></svg>
  </div>
  <div class="reason is-left" style="left:288px;top:364px">
    <h3>Certified</h3>
    <p class="serif">You receive a qualified and reliable report from a certified expert (highest acceptance by all parties)</p>
  </div>

  <div class="timeline-node" style="top:512px">
    <svg width="22" height="22" viewBox="0 0 22 22" fill="none" stroke="#4a4e54" stroke-width="1.4"><rect x="2" y="9" width="4" height="11"/><path d="M6 10 L10 3 C12 3 13 4 12.5 6 L12 9 H18 C19.5 9 20.3 10.3 20 11.5 L18.5 18.5 C18.2 19.5 17.4 20 16.5 20 H6"/></svg>
  </div>
  <div class="reason" style="left:668px;top:518px">
    <h3>Understandable</h3>
    <p class="serif">Your report will be logical and comprehensible for you and will not contain any "technical Chinese"</p>
  </div>
</section>

<section class="promise">
  <h2 class="section-title" style="top:60px">My quality promise</h2>
  <p class="promise-text serif">Should the advised date for the preparation of the report be exceeded, you<br>will receive the report free of charge (I waive my fee)</p>
  <a class="btn btn-outline" href="#">Contact now!</a>
</section>

<footer class="site-footer">
  <small>© 2018 Lukas M. Brenner. All Rights Reserved</small>
  <div class="legal-links">Data protection<span>I</span>Cookies<span>I</span>imprint</div>
  <div class="to-top">
    <svg width="10" height="12" viewBox="0 0 10 12" fill="none" stroke="#ffffff" stroke-width="1.3"><path d="M5 11V1M1 5l4-4 4 4"/></svg>
  </div>
</footer>

</body>
</html>
```